Design 4 pages for an event discovery website

This is a contest for the design of 4 pages for an events discovery website. The feature is part of the new sign-up process.

Please see the attached document for a full scope, mockups and the parent category icons.

Target Market(s)

18-35 Australian event goers

Industry/Entity Type

Events

Number of Pages Required

4 page

```html
<!DOCTYPE html>
<html lang="en">
<head>
<meta charset="utf-8">
<title>Evendo – Sign Up</title>
<link rel="stylesheet" href="https://fonts.googleapis.com/css2?family=Open+Sans:wght@400;600;700&family=Arimo:wght@400&display=swap">
<style>
:root{
  --bg-deep:#22232f;
  --bg-mid:#2b2c3a;
  --aurora-green:#2f5a4e;
  --aurora-rose:#6a3f52;
  --text:#ffffff;
  --muted:#d9dbe0;
  --panel:#363b40;
  --panel-edge:#1c1f22;
  --field:#ffffff;
  --field-text:#3a3d40;
  --error:#ff2a2a;
  --btn-top:#c9ea4a;
  --btn-bottom:#7fae1c;
  --line:#1a1b24;
}
*{box-sizing:border-box;margin:0;padding:0}
html,body{width:1200px;height:848px;overflow:hidden;background:var(--bg-deep)}
.page{position:relative;width:1200px;height:848px;overflow:hidden;font-family:"Open Sans",sans-serif;color:var(--text)}
.backdrop{position:absolute;inset:0;
  background:
   radial-gradient(ellipse 420px 300px at 1040px 160px,rgba(120,70,90,.55),transparent 70%),
   radial-gradient(ellipse 520px 220px at 300px 640px,rgba(47,90,78,.55),transparent 70%),
   radial-gradient(ellipse 300px 260px at 900px 520px,rgba(60,80,90,.35),transparent 70%),
   linear-gradient(160deg,var(--bg-mid),var(--bg-deep));}
.site-header{position:absolute;left:0;top:0;width:1200px;height:106px;border-bottom:2px solid var(--line)}
.brand{position:absolute;left:142px;top:34px;font-size:29px;font-weight:600;letter-spacing:.5px}
.search{position:absolute;left:664px;top:33px;width:234px;height:41px;border:1px solid #fff;border-radius:21px;padding-left:22px;font-size:14px;font-weight:600;line-height:39px}
.search svg{position:absolute;right:22px;top:13px}
.nav{position:absolute;top:44px;font-size:14px;font-weight:600}
.nav-signup{left:920px}.nav-sep{left:988px}.nav-login{left:1016px}
.signup-card{position:absolute;left:162px;top:166px;width:326px;height:540px;background:var(--panel);border:1px solid var(--panel-edge);border-radius:4px;box-shadow:0 3px 0 #2a2e31,0 6px 0 #1d2023,0 8px 10px rgba(0,0,0,.5)}
.handle{position:absolute;left:109px;top:22px;width:108px;height:12px;border-radius:6px;background:linear-gradient(#eee,#777);border:3px solid #111}
.card-title{position:absolute;left:0;width:100%;top:48px;text-align:center;font-size:24px;font-weight:700;text-shadow:0 2px 3px #000}
.field{position:absolute;left:29px;width:266px;height:36px;background:var(--field);border:1px solid #111;border-radius:4px;box-shadow:inset 0 3px 5px rgba(0,0,0,.35);font-family:Arimo,sans-serif;font-size:13px;color:var(--field-text);padding-left:15px;line-height:34px}
.field-error{position:absolute;left:35px;font-family:Arimo,sans-serif;font-size:9px;color:var(--error)}
.submit{position:absolute;left:71px;top:460px;width:185px;height:47px;border-radius:3px;background:linear-gradient(var(--btn-top),var(--btn-bottom));box-shadow:0 3px 0 #4d6e10,0 5px 6px rgba(0,0,0,.5);text-align:center;line-height:47px;font-size:21px;font-weight:700;text-shadow:0 2px 2px rgba(0,0,0,.5)}
.benefits{position:absolute;left:590px;top:270px}
.benefits h2{font-size:26px;font-weight:700;margin-left:1px}
.benefit-list{list-style:none;margin-top:18px;font-family:Arimo,sans-serif;font-size:14px}
.benefit-list li{position:relative;height:35.6px;padding-left:19px}
.benefit-list svg{position:absolute;left:0;top:3px}
.site-footer{position:absolute;left:0;top:770px;width:1200px;height:78px;border-top:3px solid var(--line);background:rgba(30,31,40,.6)}
.copyright{position:absolute;left:142px;top:31px;font-family:Arimo,sans-serif;font-size:12px}
.social{position:absolute;top:24px;width:36px;height:36px;border:1px solid #fff;border-radius:50%}
</style>
</head>
<body>
<div class="page">
  <div class="backdrop" role="img" aria-label="Dark night-sky backdrop with soft green and rose aurora light trails"></div>

  <header class="site-header">
    <div class="brand">EVENDO</div>
    <div class="search">Search
      <svg width="12" height="12" viewBox="0 0 12 12"><circle cx="5" cy="5" r="3.6" fill="none" stroke="#fff" stroke-width="2"/><line x1="7.6" y1="7.6" x2="11" y2="11" stroke="#fff" stroke-width="2.2"/></svg>
    </div>
    <span class="nav nav-signup">SIGN UP</span>
    <span class="nav nav-sep">|</span>
    <span class="nav nav-login">LOG IN</span>
  </header>

  <section class="signup-card">
    <div class="handle"></div>
    <div class="card-title">SIGN UP</div>
    <div class="field" style="top:93px">User Name :</div>
    <div class="field-error" style="top:131px">user name already exist</div>
    <div class="field" style="top:151px">Email Address :</div>
    <div class="field-error" style="top:188px">email address already exist</div>
    <div class="field" style="top:204px">Password :</div>
    <div class="field" style="top:250px">Conform Password :</div>
    <div class="field" style="top:296px">First Name&nbsp; :</div>
    <div class="field" style="top:342px">Last Name :</div>
    <div class="field" style="top:388px">Date of Birth :</div>
    <div class="submit">SIGN UP</div>
  </section>

  <section class="benefits">
    <h2>OUR BENEFITS</h2>
    <ul class="benefit-list">
      <li><svg width="9" height="12" viewBox="0 0 9 12"><path d="M2 1l5 5-5 5" fill="none" stroke="#fff" stroke-width="2.5"/></svg>Get personalised event recommendations</li>
      <li><svg width="9" height="12" viewBox="0 0 9 12"><path d="M2 1l5 5-5 5" fill="none" stroke="#fff" stroke-width="2.5"/></svg>Get notified about your favourite events - never miss out again</li>
      <li><svg width="9" height="12" viewBox="0 0 9 12"><path d="M2 1l5 5-5 5" fill="none" stroke="#fff" stroke-width="2.5"/></svg>Follow all your favourite artists, musicians, teams and players in one place</li>
      <li><svg width="9" height="12" viewBox="0 0 9 12"><path d="M2 1l5 5-5 5" fill="none" stroke="#fff" stroke-width="2.5"/></svg>Follow your favourite local venues to know everything happening there</li>
      <li><svg width="9" height="12" viewBox="0 0 9 12"><path d="M2 1l5 5-5 5" fill="none" stroke="#fff" stroke-width="2.5"/></svg>Get curated news and feature content on your favourite artists (coming soon)</li>
      <li><svg width="9" height="12" viewBox="0 0 9 12"><path d="M2 1l5 5-5 5" fill="none" stroke="#fff" stroke-width="2.5"/></svg>Invite your mates to events via Friendlink (Friendlink sign-up only)</li>
    </ul>
  </section>

  <footer class="site-footer">
    <div class="copyright">© Copy Rights 2015 Evendo.All Rights Reserved.</div>
    <span class="social" style="left:840px" aria-label="Social link"></span>
    <span class="social" style="left:886px" aria-label="Social link"></span>
    <span class="social" style="left:931px" aria-label="Social link"></span>
    <span class="social" style="left:976px" aria-label="Social link"></span>
    <span class="social" style="left:1023px" aria-label="Social link"></span>
  </footer>
</div>
</body>
</html>
```